Redesign of business card for Cedar Ridge Mechanical

We are looking for a new design for our business cards for Cedar Ridge Mechanical. We are a plumbing & HVAC construction company, operating on the West Coast of Canada and USA. Logo attached.
Industry/Entity Type
Construction - Plumbing & HVAC
Contact Information for Business Card
Name, address, phone numbers, email, website address
Look and feel
Each slider illustrates characteristics of the customer's brand and the style your logo design should communicate.

```html
<!DOCTYPE html>
<html lang="en">
<head>
<meta charset="utf-8">
<title>Cedar Ridge Mechanical – Business Card</title>
<link rel="stylesheet" href="https://fonts.googleapis.com/css2?family=Poppins:wght@300;400;500;700&display=swap">
<style>
  :root {
    --backdrop: #232323;
    --card-ink: #0b0b0b;
    --card-paper: #e3e4e4;
    --emboss: #cfd0d0;
    --text: #111111;
    --rule: #6a6a6a;
  }
  * { margin: 0; padding: 0; box-sizing: border-box; }
  html, body { width: 1200px; height: 711px; overflow: hidden; }
  body {
    background: var(--backdrop);
    font-family: "Poppins", sans-serif;
    color: var(--text);
    position: relative;
  }
  .card {
    position: absolute;
    top: 207px;
    width: 520px;
    height: 297px;
    border-radius: 22px;
    overflow: hidden;
    background: var(--card-ink);
  }
  .card--back { left: 50px; }
  .card--front { left: 630px; }
  .card__shape {
    position: absolute;
    inset: 0;
    width: 100%;
    height: 100%;
  }
  .brand {
    position: absolute;
    display: flex;
    align-items: center;
    gap: 12px;
    font-weight: 700;
    text-transform: uppercase;
    line-height: 1.1;
  }
  .brand__mark { flex: none; }
  .card--back .brand {
    left: 120px; top: 112px;
    font-size: 28px;
    color: var(--emboss);
  }
  .card--back .brand__mark { width: 34px; height: 34px; background: var(--emboss); }
  .card--front .brand {
    left: 40px; top: 120px;
    width: 200px;
    font-size: 17px;
    color: var(--text);
  }
  .card--front .brand__mark { width: 24px; height: 24px; background: var(--text); }
  .divider {
    position: absolute;
    left: 248px; top: 72px;
    width: 1px; height: 120px;
    background: var(--rule);
  }
  .person { position: absolute; left: 270px; top: 58px; }
  .person__name { font-size: 24px; font-weight: 300; line-height: 1.1; }
  .person__name strong { font-weight: 700; }
  .person__title { font-size: 12px; font-weight: 500; margin-top: 2px; }
  .contacts { list-style: none; margin-top: 16px; font-size: 12.5px; font-weight: 400; }
  .contacts li { display: flex; align-items: center; gap: 8px; margin-bottom: 4px; }
  .contacts svg { width: 13px; height: 13px; flex: none; }
  .address {
    position: absolute;
    left: 0; right: 0; bottom: 34px;
    text-align: center;
    font-size: 13px;
  }
</style>
</head>
<body>

<section class="card card--back" aria-label="Card back">
  <svg class="card__shape" viewBox="0 0 520 297" preserveAspectRatio="none">
    <ellipse cx="250" cy="150" rx="280" ry="215" transform="rotate(-14 250 150)" fill="var(--card-paper)"/>
  </svg>
  <div class="brand"><span class="brand__mark"></span><span>Cedar Ridge<br>Mechanical</span></div>
</section>

<section class="card card--front" aria-label="Card front">
  <svg class="card__shape" viewBox="0 0 520 297" preserveAspectRatio="none">
    <ellipse cx="250" cy="150" rx="280" ry="215" transform="rotate(-14 250 150)" fill="var(--card-paper)"/>
  </svg>
  <div class="brand"><span class="brand__mark"></span><span>Cedar Ridge<br>Mechanical</span></div>
  <div class="divider"></div>
  <div class="person">
    <p class="person__name"><strong>Marta</strong> Kovalova</p>
    <p class="person__title">Founder &amp; CEO</p>
    <ul class="contacts">
      <li><svg viewBox="0 0 24 24"><path d="M6.6 10.8a15 15 0 0 0 6.6 6.6l2.2-2.2a1 1 0 0 1 1-.25 11.4 11.4 0 0 0 3.6.57 1 1 0 0 1 1 1V20a1 1 0 0 1-1 1A17 17 0 0 1 3 4a1 1 0 0 1 1-1h3.5a1 1 0 0 1 1 1c0 1.25.2 2.45.57 3.57a1 1 0 0 1-.25 1z" fill="currentColor"/></svg>(604) 555-0187</li>
      <li><svg viewBox="0 0 24 24"><rect x="3" y="5" width="18" height="14" rx="2" fill="currentColor"/><path d="M4 7l8 6 8-6" stroke="#e3e4e4" stroke-width="1.6" fill="none"/></svg>info@cedarridgemech.com</li>
      <li><svg viewBox="0 0 24 24"><circle cx="12" cy="12" r="9" fill="none" stroke="currentColor" stroke-width="2"/><path d="M3 12h18M12 3c3 3 3 15 0 18M12 3c-3 3-3 15 0 18" stroke="currentColor" stroke-width="1.6" fill="none"/></svg>www.cedarridgemech.com</li>
    </ul>
  </div>
  <p class="address">1840 Harbor Ln. Suite 300 Portland, OR 97205</p>
</section>

</body>
</html>
```